Postcard Design Project A Healthy reminder

Dr.'s Dhelpit and Sirel dunwat. Internal Medicine/Family practice. This postcard will be for our patients that we have not seen in a while. Also we need another postcard (the one your designing) with a different heading for New patient's. Do you offer a price break for that? The only thing we would need to change is the heading. Please let me know. Thank you so much! Also can you use the map on the last postcard and our logo I made? I cant find it. Please feel free to call me or email me.

```html
<!DOCTYPE html>
<html lang="en">
<head>
<meta charset="utf-8">
<title>A Healthy Reminder – Postcard</title>
<link href="https://fonts.googleapis.com/css2?family=Open+Sans:ital,wght@0,300;0,400;0,600;0,700;0,800;1,300&family=Montserrat:ital,wght@1,300;1,800;1,900&display=swap" rel="stylesheet">
<style>
  :root{
    --bg:#9fd3d0;
    --red:#a50d0d;
    --red-bright:#c81414;
    --ink:#1b1b1b;
    --grey:#bdbdbd;
    --white:#ffffff;
    --dark:#232323;
  }
  *{margin:0;padding:0;box-sizing:border-box}
  html,body{width:1200px;height:891px;overflow:hidden}
  body{background:var(--bg);font-family:"Open Sans",sans-serif;position:relative}
  .card{position:absolute;top:245px;width:570px;height:400px;background:var(--white);box-shadow:0 6px 18px rgba(0,0,0,.18);overflow:hidden}
  .card--front{left:20px}
  .card--back{left:610px}
  .card__art{position:absolute;inset:0;width:570px;height:400px}

  /* front */
  .brand{position:absolute;left:36px;top:22px;width:190px;text-align:center}
  .brand__mark{display:block;width:24px;height:24px;border:2px solid var(--red);margin:0 auto 5px}
  .brand__name{font-weight:600;font-size:14px;color:var(--ink)}
  .brand__tag{font-weight:600;font-size:7px;letter-spacing:.6px;color:var(--ink);margin-top:2px}
  .headline{position:absolute;left:36px;top:98px;color:var(--ink)}
  .headline__lead{font-weight:300;font-size:21px;line-height:27px}
  .headline__lead strong{font-weight:800;color:var(--red)}
  .headline__big{font-weight:800;font-size:40px;line-height:42px;margin-top:4px;letter-spacing:.5px}
  .headline__exam{font-weight:800;font-size:54px;line-height:54px;color:var(--red)}
  .contact{position:absolute;left:32px;top:302px;color:var(--white)}
  .contact__row{display:flex;align-items:flex-start;gap:7px}
  .contact__addr{font-size:13px;line-height:17px}
  .contact__phone{font-weight:700;font-size:22px;line-height:30px;margin-top:3px;align-items:center}
  .contact__web{font-size:13px;line-height:18px;margin-top:1px;align-items:center}
  .contact svg{flex:none}

  /* back */
  .doctors{position:absolute;left:28px;top:14px;font-family:"Montserrat",sans-serif;font-style:italic;font-weight:900;font-size:19px;line-height:22px;color:var(--red-bright)}
  .doctors__and{font-weight:300;color:var(--ink)}
  .callnow{position:absolute;left:26px;top:178px;font-family:"Montserrat",sans-serif;font-style:italic;font-weight:900;color:var(--white);font-size:23px;line-height:25px}
  .visit{position:absolute;left:26px;top:250px;color:var(--white);font-family:"Montserrat",sans-serif;font-style:italic}
  .visit__label{font-weight:800;font-size:9px;display:flex;align-items:center;gap:6px}
  .visit__dot{width:10px;height:10px;border-radius:50%;background:#3b5ea8;display:inline-block}
  .visit__url{font-weight:300;font-size:10px;margin-top:3px}
  .visit__loc{font-weight:300;font-size:12px;margin-top:6px}
  .visit__corner{font-weight:800;font-size:12px}
</style>
</head>
<body>

<section class="card card--front">
  <svg class="card__art" viewBox="0 0 570 400">
    <defs>
      <linearGradient id="hallTone" x1="0" y1="0" x2="1" y2="1">
        <stop offset="0" stop-color="#d9c3a6"/>
        <stop offset=".5" stop-color="#ece6dc"/>
        <stop offset="1" stop-color="#b7a48e"/>
      </linearGradient>
    </defs>
    <rect width="570" height="400" fill="#f3f3f3"/>
    <path role="img" aria-label="Photo of two doctors in white coats reviewing a chart in a clinic hallway" d="M326 0 Q236 200 316 400 L570 400 L570 0 Z" fill="url(#hallTone)"/>
    <path d="M320 0 Q230 200 310 400" fill="none" stroke="var(--grey)" stroke-width="6"/>
    <path d="M310 0 Q220 200 300 400" fill="none" stroke="var(--red)" stroke-width="10"/>
    <path d="M0 285 Q120 250 262 300 Q280 350 296 400 L0 400 Z" fill="var(--red)"/>
  </svg>

  <div class="brand">
    <span class="brand__mark"></span>
    <div class="brand__name">Dhelpit T. Dunwat, M.D.</div>
    <div class="brand__tag">A Primary Care Office</div>
  </div>

  <div class="headline">
    <p class="headline__lead">A healthy <strong>reminder,</strong></p>
    <p class="headline__lead">It is time for your</p>
    <p class="headline__big">ANNUAL</p>
    <p class="headline__exam">EXAM.</p>
  </div>

  <div class="contact">
    <div class="contact__row contact__addr">
      <svg width="12" height="16" viewBox="0 0 12 16"><path d="M6 1a4.5 4.5 0 0 0-4.5 4.5C1.5 9 6 15 6 15s4.5-6 4.5-9.5A4.5 4.5 0 0 0 6 1z" fill="none" stroke="#fff" stroke-width="1.4"/><circle cx="6" cy="5.5" r="1.6" fill="#fff"/></svg>
      <span>4820 N. Carvell Ave Suite 210<br>Linden Vale, Ca 93811</span>
    </div>
    <div class="contact__row contact__phone">
      <svg width="20" height="20" viewBox="0 0 22 22"><circle cx="11" cy="11" r="10" fill="none" stroke="#fff" stroke-width="1.6"/><path d="M8 6.5l2 2-1.2 1.4a7 7 0 0 0 3.3 3.3l1.4-1.2 2 2-1.3 1.5C10.5 15.5 6.5 11.5 6.5 7.8z" fill="#fff"/></svg>
      <span>(555) 284-6130</span>
    </div>
    <div class="contact__row contact__web">
      <svg width="12" height="12" viewBox="0 0 14 14"><circle cx="7" cy="7" r="6" fill="none" stroke="#fff" stroke-width="1.2"/><ellipse cx="7" cy="7" rx="2.6" ry="6" fill="none" stroke="#fff" stroke-width="1"/><path d="M1 7h12" stroke="#fff" stroke-width="1"/></svg>
      <span>www.dhelpitdunwatmd.com</span>
    </div>
  </div>
</section>

<section class="card card--back">
  <svg class="card__art" viewBox="0 0 570 400">
    <defs>
      <clipPath id="discClip"><circle cx="40" cy="200" r="300"/></clipPath>
      <linearGradient id="mapTone" x1="0" y1="0" x2="1" y2="0">
        <stop offset="0" stop-color="#cfe6c4"/>
        <stop offset="1" stop-color="#e8e8e4"/>
      </linearGradient>
      <linearGradient id="officeTone" x1="0" y1="0" x2="0" y2="1">
        <stop offset="0" stop-color="#8a9a6a"/>
        <stop offset=".55" stop-color="#9a9a94"/>
        <stop offset="1" stop-color="#6f9a4a"/>
      </linearGradient>
    </defs>
    <rect width="570" height="400" fill="#fff"/>
    <g clip-path="url(#discClip)">
      <rect x="0" y="0" width="570" height="62" fill="#f4f4f4"/>
      <rect role="img" aria-label="Street map showing the office location" x="0" y="62" width="570" height="110" fill="url(#mapTone)"/>
      <rect x="0" y="172" width="570" height="62" fill="var(--red)"/>
      <rect x="0" y="234" width="570" height="166" fill="var(--dark)"/>
    </g>
    <circle cx="40" cy="200" r="304" fill="none" stroke="var(--red)" stroke-width="9"/>
    <circle cx="40" cy="200" r="312" fill="none" stroke="var(--grey)" stroke-width="5"/>
    <circle role="img" aria-label="Photo of the office building entrance" cx="292" cy="214" r="56" fill="url(#officeTone)" stroke="var(--red)" stroke-width="6"/>
    <rect x="462" y="28" width="80" height="52" fill="none" stroke="#555" stroke-width="1"/>
    <line x1="360" y1="222" x2="540" y2="222" stroke="#444" stroke-width="1"/>
    <line x1="360" y1="262" x2="540" y2="262" stroke="#444" stroke-width="1"/>
    <line x1="360" y1="302" x2="540" y2="302" stroke="#444" stroke-width="1"/>
  </svg>

  <div class="doctors">Dr.'s Dhelpit <span class="doctors__and">and</span><br>Sirel Dunwat</div>

  <div class="callnow">CALL NOW<br>(555) 284-6130</div>

  <div class="visit">
    <div class="visit__label">VISIT US ONLINE <span class="visit__dot"></span></div>
    <div class="visit__url">www.socialpage.com/doctorsdunwat</div>
    <div class="visit__loc">Located On The</div>
    <div class="visit__corner">SE corner of Carvell and Birch.</div>
  </div>
</section>

</body>
</html>
```